Website for "Bright Morrow Ltd" cleaning bsuiness

We require a website to expose our business to the local market. We want to provide background on who we are and what we do but in an easily digestible way. We clean domestic and commercial premises and want to provide a list of all of our services to potential customers. We operate out of Warrington in the UK.

We would like the website to be animated in some way so that the experience of using it is not dull or mundane. This website needs to be an extension of our company.

Target Market(s)

30 - 60 year olds for Domestic plus commercial clients

Industry/Entity Type

Cleaning Service

Coding

Coded - Design and coding required

Number of Pages Required

4 page

Font styles to use
Sans Serif

Colors
0455a3
3176b5
85acd3
cfdeed
ffffff
000000
1b1b1b
c8c8c8
757575

Requirements
Must have
• Logo which has been provided. Theme based around the logo and its colours. Simple layout to avoid confusion.
Nice to have
• Animations where possible to impress the customer.
Should not have
• any pictures of cleaning equipment, fairies, maids etc

```html
<!DOCTYPE html>
<html lang="en">
<head>
<meta charset="utf-8">
<title>Bright Morrow Ltd – Professional Cleaning Service</title>
<link href="https://fonts.googleapis.com/css2?family=Mulish:wght@300;400;600;700&display=swap" rel="stylesheet">
<style>
  :root{
    --blue-deep:#0455a3;
    --blue-mid:#3176b5;
    --blue-soft:#85acd3;
    --blue-pale:#cfdeed;
    --white:#ffffff;
    --black:#000000;
    --ink:#1b1b1b;
    --grey-line:#c8c8c8;
    --grey-text:#757575;
    --button:#1a6fd0;
    --wood:#9a7a52;
  }
  *{box-sizing:border-box;margin:0;padding:0}
  html,body{width:1200px;height:3442px;overflow:hidden}
  body{position:relative;font-family:"Mulish",Arial,sans-serif;color:var(--ink);background:var(--white)}
  .abs{position:absolute}
  a{color:inherit;text-decoration:none}

  /* ---------- Hero ---------- */
  .hero{position:absolute;left:0;top:0;width:1200px;height:787px;overflow:hidden}
  .hero-photo{position:absolute;inset:0;background:linear-gradient(180deg,#5d6b78 0%,#3e4955 45%,#2a323b 100%)}
  .hero-band{position:absolute;left:0;top:0}
  .nav{position:absolute;top:70px;left:0;width:1200px;height:36px}
  .nav a{position:absolute;top:0;height:36px;line-height:36px;font-size:15px;color:var(--white);font-weight:400}
  .nav a.active{background:rgba(133,172,211,.45);border-radius:18px;padding:0 18px;box-shadow:inset 0 1px 0 rgba(255,255,255,.3)}
  .brand-badge{position:absolute;width:174px;height:174px;border-radius:50%;background:var(--white);display:flex;flex-direction:column;align-items:center;justify-content:center;text-align:center;color:var(--blue-deep);font-weight:700;font-size:22px;line-height:1.1;box-shadow:0 0 0 7px var(--black)}
  .hero-title{position:absolute;top:425px;left:0;width:1200px;text-align:center;color:var(--white);font-weight:300;font-size:46px}
  .hero-sub{position:absolute;top:478px;left:0;width:1200px;text-align:center;color:var(--white);font-size:16px}
  .btn{position:absolute;background:var(--button);color:var(--white);font-size:12px;text-transform:uppercase;text-align:center;border-radius:4px;letter-spacing:.5px}
  .hero-dots{position:absolute;top:683px;left:550px;display:flex;gap:14px}
  .hero-dots span{width:13px;height:13px;border-radius:50%;background:var(--white)}
  .hero-dots span.current{background:var(--blue-mid)}

  /* ---------- Intro ---------- */
  .intro{position:absolute;left:0;top:787px;width:1200px;height:477px;background:linear-gradient(90deg,#8e6f48,#a8875c 30%,#94744c 60%,#a4845a)}
  .intro-heading{position:absolute;left:202px;top:96px;color:var(--white);font-size:28px;font-weight:400;line-height:32px}
  .intro-rule{position:absolute;left:202px;top:170px;width:227px;height:4px;background:var(--blue-mid)}
  .intro-text{position:absolute;left:202px;top:204px;width:320px;color:var(--white);font-size:14px;line-height:25px}
  .intro-video{position:absolute;left:555px;top:99px;width:445px;height:289px;border:9px solid var(--white);box-shadow:0 8px 20px rgba(0,0,0,.35);background:linear-gradient(160deg,#e8ecef,#b9c2c8 55%,#7a5a3e)}
  .intro-video svg{position:absolute;left:184px;top:98px}

  /* ---------- Services ---------- */
  .services{position:absolute;left:0;top:1264px;width:1200px;height:702px;background:#f3f3f3}
  .section-title{position:absolute;left:0;width:1200px;text-align:center;font-size:28px;font-weight:400}
  .services .section-title{top:82px;color:var(--blue-deep)}
  .services-rule{position:absolute;left:202px;top:145px;width:796px;height:1px;background:#e2e2e2}
  .service-card{position:absolute;top:186px;width:388px;height:404px;background:var(--black);color:var(--white);text-align:center;overflow:hidden}
  .service-photo{position:absolute;left:0;top:0;width:100%;height:230px}
  .service-icon{position:absolute;top:92px;left:166px}
  .service-name{position:absolute;top:148px;width:100%;font-size:26px;font-weight:400}
  .service-text{position:absolute;top:212px;left:40px;width:308px;font-size:13.5px;line-height:27px}

  /* ---------- Testimonials ---------- */
  .testimonials{position:absolute;left:0;top:1966px;width:1200px;height:516px;background:linear-gradient(90deg,#3a6ca8,#4b7fbc 50%,#6a95c6);overflow:hidden}
  .testimonials .section-title{top:50px;color:var(--white)}
  .quote-box{position:absolute;left:271px;top:133px;width:727px;height:218px;background:rgba(20,40,70,.55)}
  .quote-photo{position:absolute;left:20px;top:23px;width:218px;height:165px;border:5px solid var(--white);background:linear-gradient(180deg,#d9d4cc,#b4a89a)}
  .quote-text{position:absolute;left:275px;top:20px;width:410px;color:var(--white);font-size:18px;line-height:28px}
  .quote-mark{position:absolute;left:677px;top:70px}
  .quote-rule{position:absolute;left:406px;top:397px;width:385px;border-top:2px dashed rgba(255,255,255,.5)}
  .quote-name{position:absolute;left:0;top:413px;width:1200px;text-align:center;color:var(--white);font-size:27px}
  .quote-role{position:absolute;left:0;top:455px;width:1200px;text-align:center;color:var(--white);font-size:14px}
  .quote-arrow{position:absolute;top:420px}

  /* ---------- News ---------- */
  .news{position:absolute;left:0;top:2482px;width:1200px;height:460px;background:var(--white)}
  .news .section-title{top:60px;color:var(--ink)}
  .news-arrow{position:absolute;top:70px}
  .news-card{position:absolute;top:154px;width:254px}
  .news-photo{position:relative;height:160px}
  .news-date{position:absolute;left:16px;top:32px;width:50px;height:78px;background:var(--blue-deep);color:var(--white);text-align:center;font-size:10px;line-height:12px;padding-top:20px;text-transform:uppercase}
  .news-meta{margin-top:18px;display:flex;align-items:center;gap:6px;font-size:10px;color:var(--ink)}
  .news-excerpt{margin-top:22px;font-size:13px;line-height:17px;color:var(--grey-text)}

  /* ---------- Footer ---------- */
  .footer{position:absolute;left:0;top:2920px;width:1200px;height:522px}
  .footer-shape{position:absolute;left:0;top:0}
  .footer-col{position:absolute;top:227px;font-size:13px;line-height:27.5px;color:var(--white)}
  .footer-col h4{font-size:13px;font-weight:400;color:var(--blue-mid);margin-bottom:6px;line-height:18px}
  .social{display:flex;gap:9px;margin-top:4px}
  .social span{width:25px;height:25px;border-radius:50%;background:var(--button)}
  .copyright{position:absolute;top:482px;left:0;width:1200px;text-align:center;color:var(--white);font-size:10px}
</style>
</head>
<body>

<header class="hero">
  <div class="hero-photo" role="img" aria-label="Photo of a bright open-plan office with desks and chairs"></div>
  <svg class="hero-band" width="1200" height="787" viewBox="0 0 1200 787" aria-hidden="true">
    <defs>
      <linearGradient id="bandFill" x1="0" y1="0" x2="0" y2="1">
        <stop offset="0" stop-color="#0a3f86"/>
        <stop offset="1" stop-color="#0455a3"/>
      </linearGradient>
    </defs>
    <path d="M0 0H1200V180Q600 270 0 180Z" fill="url(#bandFill)"/>
    <path d="M0 180Q600 270 1200 180" fill="none" stroke="#3176b5" stroke-width="3"/>
  </svg>

  <nav class="nav">
    <a class="active" style="left:190px">Welcome</a>
    <a style="left:317px">About Us</a>
    <a style="left:429px">Services</a>
    <a style="left:700px">Blog</a>
    <a style="left:775px">Testimonials</a>
    <a style="left:910px">Contact Us</a>
  </nav>
  <div class="brand-badge" style="left:514px;top:16px">Bright<br>Morrow<br>Ltd</div>

  <h1 class="hero-title">Bright Morrow</h1>
  <p class="hero-sub">We Are A Professional Cleaning Service</p>
  <a class="btn" style="left:535px;top:526px;width:128px;height:38px;line-height:38px;border-radius:10px">Learn More</a>
  <div class="hero-dots"><span class="current"></span><span></span><span></span><span></span></div>
</header>

<section class="intro">
  <h2 class="intro-heading">INTRO TO<br>BRIGHT MORROW</h2>
  <div class="intro-rule"></div>
  <p class="intro-text">Sed ut perspiciatis unde omnis iste natus error sit voluptatem accusantium doloremque laudantium, totam rem aperiam, eaque ipsa quae ab illo inventore veritatis et quasi architecto beatae vitae dicta sunt explicabo.</p>
  <a class="btn" style="left:202px;top:349px;width:133px;height:34px;line-height:34px;border-radius:2px;font-size:11px">Learn More</a>
  <div class="intro-video" role="img" aria-label="Video still of a bright modern office with wooden floor">
    <svg width="76" height="76" viewBox="0 0 76 76" aria-hidden="true">
      <circle cx="38" cy="38" r="36" fill="rgba(49,118,181,.75)" stroke="#fff" stroke-width="2"/>
      <path d="M30 24L52 38L30 52Z" fill="none" stroke="#fff" stroke-width="3" stroke-linejoin="round"/>
    </svg>
  </div>
</section>

<section class="services">
  <h2 class="section-title">WHAT WE CLEAN</h2>
  <div class="services-rule"></div>

  <article class="service-card" style="left:202px">
    <div class="service-photo" role="img" aria-label="Photo of a tidy home bedroom" style="background:linear-gradient(180deg,#8c7a6e 0%,#5a4a42 50%,#000 100%)"></div>
    <svg class="service-icon" width="56" height="48" viewBox="0 0 56 48" aria-hidden="true">
      <path d="M4 22L28 4L52 22" fill="none" stroke="#3176b5" stroke-width="4"/>
      <rect x="11" y="20" width="34" height="26" fill="#3176b5"/>
      <rect x="17" y="26" width="7" height="7" fill="#000"/><rect x="32" y="26" width="7" height="7" fill="#000"/>
      <rect x="24" y="34" width="8" height="12" fill="#000"/>
    </svg>
    <h3 class="service-name">Domestic</h3>
    <p class="service-text">Sed ut perspiciatis unde omnis iste natus error sit voluptatem accusantium doloremque laudantium, totam rem aperiam, eaque ipsa quae ab illo inventore veritatis et quasi architecto beatae vitae dicta</p>
  </article>

  <article class="service-card" style="left:610px">
    <div class="service-photo" role="img" aria-label="Photo of a glass-walled commercial corridor" style="background:linear-gradient(180deg,#9aa3a8 0%,#5e666b 50%,#000 100%)"></div>
    <svg class="service-icon" width="56" height="48" viewBox="0 0 56 48" aria-hidden="true">
      <rect x="6" y="4" width="24" height="42" fill="#3176b5"/>
      <rect x="30" y="16" width="20" height="30" fill="#3176b5"/>
      <g fill="#000"><rect x="11" y="10" width="5" height="5"/><rect x="20" y="10" width="5" height="5"/><rect x="11" y="20" width="5" height="5"/><rect x="20" y="20" width="5" height="5"/><rect x="11" y="30" width="5" height="5"/><rect x="20" y="30" width="5" height="5"/><rect x="35" y="22" width="5" height="5"/><rect x="35" y="32" width="5" height="5"/></g>
    </svg>
    <h3 class="service-name">Commercial</h3>
    <p class="service-text">Sed ut perspiciatis unde omnis iste natus error sit voluptatem accusantium doloremque laudantium, totam rem aperiam, eaque ipsa quae ab illo inventore veritatis et quasi architecto beatae vitae dicta</p>
  </article>
</section>

<section class="testimonials" role="region" aria-label="Testimonials over a faint office photo">
  <h2 class="section-title">TESTIMONIALS</h2>
  <div class="quote-box">
    <div class="quote-photo" role="img" aria-label="Portrait photo of a smiling client"></div>
    <p class="quote-text">Sed ut perspiciatis unde omnis iste naus error sit voluptatem accusantium doloremque laudantium, totam rem aperiam, eaque ipsa quae ab illo inventore veritatis et quasi architecto beatae vitae dicta sunt explicabo.</p>
    <svg class="quote-mark" width="78" height="78" viewBox="0 0 78 78" aria-hidden="true">
      <circle cx="39" cy="39" r="39" fill="#3176b5"/>
      <path d="M22 48V38Q22 28 32 26V31Q27 33 27 37H33V48ZM41 48V38Q41 28 51 26V31Q46 33 46 37H52V48Z" fill="#fff"/>
    </svg>
  </div>
  <div class="quote-rule"></div>
  <svg class="quote-arrow" style="left:416px" width="16" height="22" viewBox="0 0 16 22" aria-hidden="true"><path d="M12 3L4 11L12 19" fill="none" stroke="#fff" stroke-width="3"/></svg>
  <p class="quote-name">Daniel Hartley</p>
  <p class="quote-role">Company Name</p>
  <svg class="quote-arrow" style="left:766px" width="16" height="22" viewBox="0 0 16 22" aria-hidden="true"><path d="M4 3L12 11L4 19" fill="none" stroke="#fff" stroke-width="3"/></svg>
</section>

<section class="news">
  <svg class="news-arrow" style="left:200px" width="14" height="20" viewBox="0 0 14 20" aria-hidden="true"><path d="M10 3L3 10L10 17" fill="none" stroke="#1b1b1b" stroke-width="3"/></svg>
  <h2 class="section-title">NEWS</h2>
  <svg class="news-arrow" style="left:986px" width="14" height="20" viewBox="0 0 14 20" aria-hidden="true"><path d="M4 3L11 10L4 17" fill="none" stroke="#1b1b1b" stroke-width="3"/></svg>

  <article class="news-card" style="left:202px">
    <div class="news-photo" role="img" aria-label="Photo of a modern office interior" style="background:linear-gradient(160deg,#c9cdd0,#7b8590)"><div class="news-date">Oct<br>19th<br>2016</div></div>
    <p class="news-meta"><svg width="8" height="10" viewBox="0 0 8 10" aria-hidden="true"><circle cx="4" cy="3" r="2.5" fill="#0455a3"/><path d="M0 10Q4 4 8 10Z" fill="#0455a3"/></svg>Posted By Bright Morrow</p>
    <p class="news-excerpt">Sed ut perspiciatis unde omnis iste nous error sit voluptatem accusantium doloremque...</p>
  </article>
  <article class="news-card" style="left:475px">
    <div class="news-photo" role="img" aria-label="Photo of a bright living room" style="background:linear-gradient(160deg,#eceae6,#a7a39d)"><div class="news-date">Oct<br>19th<br>2016</div></div>
    <p class="news-meta"><svg width="8" height="10" viewBox="0 0 8 10" aria-hidden="true"><circle cx="4" cy="3" r="2.5" fill="#0455a3"/><path d="M0 10Q4 4 8 10Z" fill="#0455a3"/></svg>Posted By Bright Morrow</p>
    <p class="news-excerpt">Sed ut perspiciatis unde omnis iste nous error sit voluptatem accusantium doloremque...</p>
  </article>
  <article class="news-card" style="left:748px">
    <div class="news-photo" role="img" aria-label="Photo of people working together at a table" style="background:linear-gradient(160deg,#d8b48e,#a5623e)"><div class="news-date">Oct<br>19th<br>2016</div></div>
    <p class="news-meta"><svg width="8" height="10" viewBox="0 0 8 10" aria-hidden="true"><circle cx="4" cy="3" r="2.5" fill="#0455a3"/><path d="M0 10Q4 4 8 10Z" fill="#0455a3"/></svg>Posted By Bright Morrow</p>
    <p class="news-excerpt">Sed ut perspiciatis unde omnis iste nous error sit voluptatem accusantium doloremque...</p>
  </article>
</section>

<footer class="footer">
  <svg class="footer-shape" width="1200" height="522" viewBox="0 0 1200 522" aria-hidden="true">
    <path d="M0 20Q600 110 1200 20V522H0Z" fill="#0455a3"/>
    <path d="M0 34Q600 124 1200 34V522H0Z" fill="#121212"/>
  </svg>
  <div class="brand-badge" style="left:514px;top:21px">Bright<br>Morrow<br>Ltd</div>

  <div class="footer-col" style="left:209px">
    <h4>Quick Links</h4>
    Welcome<br>About Us<br>Services<br>Blog<br>Testimonials<br>Contact Us
  </div>
  <div class="footer-col" style="left:388px">
    <h4>Other Links</h4>
    Terms Of Service<br>Privacy Policy
  </div>
  <div class="footer-col" style="left:569px">
    <h4>Contact Us</h4>
    Unit 4, Larchfield Court,<br>27 Orchard Lane,<br>Warrington, WA1 4TX,<br>United Kingdom<br><br>+44 1925 000 318
  </div>
  <div class="footer-col" style="left:819px">
    <h4>Get In Touch</h4>
    <div class="social"><span></span><span></span><span></span><span></span></div>
  </div>
  <p class="copyright">© 2016 Company Name &nbsp;|&nbsp; All Rights Reserved</p>
</footer>

</body>
</html>
```